Insurance Agency website design for Brellow Cover Insurance, LP

Build a website for Brellow Cover Insurance, LP which sells Homeowners, Auto, Renters, Condo, Flood, Disability, Life, Umbrella, and health insurance. We need the coolest insurance agency website out there to get quotes, contact us, or get additional information. Please list the following insurance companies we work with: Varnix, Ostle, Meridale Mutual, Quillor, Dunmarrow, KGZ, and Pellwick.

Make a design similar to https://www.fernagentry.com/

Selling personal insurance policies

```html
<!DOCTYPE html>
<html lang="en">
<head>
<meta charset="utf-8">
<title>Brellow Cover Insurance, LP</title>
<link href="https://fonts.googleapis.com/css2?family=Montserrat:wght@400;500;600;700;800&display=swap" rel="stylesheet">
<style>
:root{
  --navy:#0b2a80;
  --navy-deep:#0a2569;
  --green:#479c14;
  --green-light:#7cc142;
  --ink:#1e2437;
  --muted:#7b8090;
  --line:#d9dce3;
  --star:#f2a33a;
  --paper:#ffffff;
}
*{box-sizing:border-box;margin:0;padding:0}
html,body{width:1200px;height:4615px;overflow:hidden;background:var(--paper)}
body{position:relative;font-family:'Montserrat',sans-serif;color:var(--ink)}
.abs{position:absolute}
.btn{position:absolute;display:flex;align-items:center;justify-content:center;font-weight:600;font-size:14px;color:#fff;border-radius:3px;text-decoration:none}
.btn-navy{background:var(--navy)}
.btn-green{background:var(--green-light)}
.eyebrow{position:absolute;font-size:12px;font-weight:600;letter-spacing:1.5px;color:var(--green-light);text-transform:uppercase}
.section-title{position:absolute;font-weight:700;font-size:29px;color:var(--navy)}
.center{left:0;width:1200px;text-align:center}

/* hero */
.hero{left:0;top:0;width:1200px;height:609px;background:linear-gradient(90deg,#dfe6ea 0%,#e8edf0 45%,#c9d3da 100%)}
.hero-photo{left:540px;top:0;width:660px;height:609px;background:linear-gradient(100deg,rgba(225,231,235,0) 0%,#b8c6d1 30%,#8b9caa 65%,#c4ced6 100%)}
.topbar{top:-6px;font-size:12px;color:var(--ink)}
.brand{left:149px;top:42px;font-weight:700;font-size:19px;color:var(--navy-deep)}
.nav{top:44px;left:541px;display:flex;gap:31px;font-size:13px;font-weight:500}
.hero h1{left:149px;top:196px;font-size:49px;line-height:59px;font-weight:700;color:#2a2f3d;letter-spacing:.5px}
.hero p{left:149px;top:322px;font-size:15px;line-height:27px;color:#2a2f3d;width:360px}

/* features */
.feature{top:695px;width:219px;height:211px;color:#fff;text-align:center}
.feature .ring{position:absolute;left:67px;top:40px;width:85px;height:85px;border-radius:50%;background:#fff;display:flex;align-items:center;justify-content:center}
.feature .ring svg{width:48px;height:48px}
.feature span{position:absolute;left:0;top:136px;width:219px;font-size:16px;line-height:20px}
.f-navy{background:var(--navy)}
.f-green{background:var(--green)}

/* about */
.about-block{left:149px;top:1280px;width:127px;height:191px;background:var(--navy)}
.about-photo{left:168px;top:1027px;width:367px;height:423px;background:linear-gradient(135deg,#9a8c78,#6f6a62 50%,#b9a08a);clip-path:polygon(0 0,88% 0,100% 8%,100% 100%,0 100%)}
.about-title{left:609px;top:1076px;font-size:29px}
.rule{position:absolute;height:3px;width:62px;background:var(--green-light)}
.about-copy{position:absolute;left:609px;width:455px;font-size:11.3px;line-height:20.5px;color:#6d7280}

/* solutions */
.solutions{left:0;top:1556px;width:1200px;height:791px;background:linear-gradient(180deg,#1f4f9b,#2657a3 50%,#1e4d96)}
.card{position:absolute;width:196px;height:227px;background:#fff;border-radius:3px;text-align:center}
.card .ic{position:absolute;left:70px;top:22px;width:55px;height:55px;border-radius:4px;display:flex;align-items:center;justify-content:center}
.ic-blue{background:#e7edf7}
.ic-green{background:#e6f3da}
.card h3{position:absolute;left:0;top:98px;width:196px;font-size:15px;font-weight:600;color:var(--ink)}
.card p{position:absolute;left:12px;top:128px;width:172px;font-size:10.3px;line-height:17px;color:#7b8090}

/* partners */
.partners{position:absolute;left:149px;top:2550px;width:916px;display:flex;justify-content:space-between;align-items:center}
.partner{font-size:15px;color:#1e2437;font-weight:600;letter-spacing:1px;white-space:nowrap}

/* testimonials */
.quote-card{position:absolute;top:2798px;width:444px;height:227px;background:#fff;border-radius:6px;box-shadow:0 4px 24px rgba(20,30,60,.1)}
.quote-mark{position:absolute;left:18px;top:-20px;font-size:80px;font-weight:800;color:#c5cbe0;line-height:1;font-family:Georgia,serif}
.quote-card p{position:absolute;left:25px;top:42px;width:394px;text-align:center;font-size:10.6px;line-height:22.5px;color:#7b8090}
.avatar{position:absolute;left:115px;top:148px;width:53px;height:53px;border-radius:50%;background:linear-gradient(135deg,#9b7a62,#5b4437)}
.quote-card h4{position:absolute;left:183px;top:150px;font-size:15px;color:var(--navy);font-weight:700}
.stars{position:absolute;left:183px;top:174px;display:flex;gap:3px}
.arrow{position:absolute;width:32px;height:32px;border-radius:50%;display:flex;align-items:center;justify-content:center}
.dot{position:absolute;top:3069px;width:7px;height:7px;border-radius:50%;background:#c9ccd6}

/* cta */
.cta{left:0;top:3165px;width:1200px;height:318px;background:linear-gradient(90deg,#5e9e2c,#7fb33f 45%,#5c9a33)}
.cta-title{top:3236px;font-size:29px;font-weight:700;color:#fff}
.cta-text{top:3288px;left:250px;width:700px;font-size:12.5px;line-height:23px;color:#fff;font-weight:500;text-align:center}

/* footer & contact */
.footer{left:0;top:4001px;width:1200px;height:614px;background:var(--navy)}
.contact-card{left:195px;top:3571px;width:822px;height:559px;background:#fff;border-radius:6px;box-shadow:0 4px 30px rgba(20,30,60,.1)}
.field{position:absolute;font-size:11px;color:#6d7280;border-bottom:1px solid var(--line);padding-bottom:14px}
.field b{color:#e33;font-weight:400}
.foot-brand{left:149px;top:4228px;display:flex;align-items:center;gap:8px;color:#fff}
.foot-brand .sq{width:22px;height:22px;background:var(--green-light)}
.foot-brand span{font-size:15px;font-weight:700}
.foot-text{left:348px;top:4207px;width:500px;font-size:11px;line-height:20px;color:#fff}
.social{position:absolute;top:4226px;width:35px;height:35px;border-radius:50%;background:#fff}
.social.g{background:var(--green-light)}
.foot-rule{left:149px;top:4280px;width:916px;height:1px;background:rgba(255,255,255,.25)}
.info-col{position:absolute;top:4360px;width:300px;text-align:center;color:#fff}
.info-col h5{font-size:13px;font-weight:700;margin-top:14px}
.info-col p{font-size:12px;line-height:22px;margin-top:10px;color:#dfe4f2}
.vdiv{top:4360px;width:1px;height:110px;background:rgba(255,255,255,.25)}
.copyright{top:4543px;font-size:12px;color:#fff}
</style>
</head>
<body>

<!-- Hero -->
<section class="abs hero">
  <div class="abs hero-photo" role="img" aria-label="Photo of an insurance agent shaking hands with clients across a desk"></div>
  <div class="abs topbar" style="left:148px">&#9675; &#9675; &#9675; &#9675;</div>
  <div class="abs topbar" style="left:700px">(812) 555-0143 &nbsp;&nbsp;&nbsp; info@brellowcover.com</div>
  <div class="abs brand">BRELLOW COVER INSURANCE</div>
  <nav class="abs nav">
    <span>Home</span><span>About Us</span><span>Insurance Types &#8964;</span><span>Contact Us</span>
  </nav>
  <a class="btn btn-navy" style="left:940px;top:32px;width:125px;height:41px">Get a Quote</a>
  <h1 class="abs">PROTECT WHAT<br>MATTERS MOST</h1>
  <p class="abs">Comprehensive insurance solutions for your home, vehicle, health, and loved ones</p>
  <a class="btn btn-navy" style="left:148px;top:390px;width:126px;height:42px">Get a Quote</a>
</section>

<!-- Feature tiles -->
<div class="abs feature f-navy" style="left:149px">
  <div class="ring"><svg viewBox="0 0 48 48" fill="none" stroke="#0b2a80" stroke-width="2"><rect x="12" y="8" width="22" height="30" rx="2"/><path d="M17 16h12M17 22h12M17 28h7"/><circle cx="32" cy="34" r="6"/></svg></div>
  <span>Insurance<br>Policies</span>
</div>
<div class="abs feature f-green" style="left:381px">
  <div class="ring"><svg viewBox="0 0 48 48" fill="none" stroke="#479c14" stroke-width="2"><circle cx="24" cy="24" r="18"/><circle cx="18" cy="20" r="1.5" fill="#479c14"/><circle cx="30" cy="20" r="1.5" fill="#479c14"/><path d="M16 28c4 5 12 5 16 0"/></svg></div>
  <span>1000+ Happy<br>Clients</span>
</div>
<div class="abs feature f-navy" style="left:614px">
  <div class="ring"><svg viewBox="0 0 48 48" fill="none" stroke="#0b2a80" stroke-width="2"><circle cx="24" cy="19" r="8"/><path d="M14 19a10 10 0 0 1 20 0M10 40c2-8 8-11 14-11s12 3 14 11"/></svg></div>
  <span>Professional<br>Support</span>
</div>
<div class="abs feature f-green" style="left:847px">
  <div class="ring"><svg viewBox="0 0 48 48" fill="none" stroke="#479c14" stroke-width="2"><circle cx="24" cy="24" r="16"/><circle cx="24" cy="24" r="7"/><path d="M24 4v6M24 38v6M4 24h6M38 24h6"/></svg></div>
  <span>Free Lifetime<br>Updates</span>
</div>

<!-- About -->
<div class="abs about-block"></div>
<div class="abs about-photo" role="img" aria-label="Photo of an agent handing house keys to a smiling couple"></div>
<div class="eyebrow" style="left:609px;top:1049px">Who we are</div>
<h2 class="section-title about-title">About Brellow Cover Insurance</h2>
<div class="rule" style="left:609px;top:1121px"></div>
<p class="about-copy" style="top:1152px">At Brellow Cover Insurance, we're dedicated to providing you with reliable, comprehensive insurance solutions tailored to your needs. Our mission is simple: to offer you peace of mind with the protection you deserve. We specialize in home, auto, health, and life insurance, and our experienced team is committed to helping you find the right coverage for every stage of life.</p>
<p class="about-copy" style="top:1272px">Founded with a focus on customer satisfaction, Brellow Cover Insurance has grown to become a trusted partner in securing what matters most. With years of industry expertise, we prioritize clear communication and personalized service. Our clients' needs are at the heart of everything we do, and we work tirelessly to ensure they have the best protection available.</p>
<a class="btn btn-green" style="left:609px;top:1407px;width:137px;height:43px">Learn More</a>

<!-- Solutions -->
<section class="abs solutions"></section>
<div class="eyebrow center" style="top:1613px">Our insurances</div>
<h2 class="section-title center" style="top:1638px;color:#fff">Our Various Insurance Solutions</h2>

<div class="card" style="left:82px;top:1729px">
  <div class="ic ic-blue"><svg width="32" height="32" viewBox="0 0 32 32" fill="none" stroke="#1d4f9a" stroke-width="2"><path d="M4 15L16 5l12 10M8 13v14h16V13"/><circle cx="16" cy="19" r="3"/></svg></div>
  <h3>Homeowners</h3>
  <p>Protect your home and belongings from damage, theft, or disaster with comprehensive homeowners coverage.</p>
</div>
<div class="card" style="left:292px;top:1729px">
  <div class="ic ic-green"><svg width="32" height="32" viewBox="0 0 32 32" fill="none" stroke="#479c14" stroke-width="2"><path d="M5 20l3-8h16l3 8v5H5z"/><circle cx="10" cy="21" r="1.5"/><circle cx="22" cy="21" r="1.5"/></svg></div>
  <h3>Auto Insurance</h3>
  <p>Safeguard your vehicle against accidents, theft, or damage, ensuring you're covered on the road.</p>
</div>
<div class="card" style="left:502px;top:1729px">
  <div class="ic ic-blue"><svg width="32" height="32" viewBox="0 0 32 32" fill="none" stroke="#1d4f9a" stroke-width="2"><path d="M5 14L16 6l11 8M8 13v14h16V13M13 27v-7h6v7"/></svg></div>
  <h3>Renters Insurance</h3>
  <p>Protect personal belongings in a rental space, covering damage, theft, or loss due to disasters.</p>
</div>
<div class="card" style="left:712px;top:1729px">
  <div class="ic ic-green"><svg width="32" height="32" viewBox="0 0 32 32" fill="none" stroke="#479c14" stroke-width="2"><rect x="9" y="4" width="14" height="24"/><path d="M13 9h2M17 9h2M13 14h2M17 14h2M13 19h2M17 19h2"/></svg></div>
  <h3>Condo Insurance</h3>
  <p>Cover your condo unit and personal property, filling the gap not covered by the building's insurance.</p>
</div>
<div class="card" style="left:922px;top:1729px">
  <div class="ic ic-blue"><svg width="32" height="32" viewBox="0 0 32 32" fill="none" stroke="#1d4f9a" stroke-width="2"><path d="M4 16a12 10 0 0 1 24 0zM16 16v9a3 3 0 0 1-6 0"/><path d="M16 6V4"/></svg></div>
  <h3>Umbrella Insurance</h3>
  <p>Extend liability protection beyond your home and auto limits, guarding your savings from major claims.</p>
</div>
<div class="card" style="left:187px;top:1978px">
  <div class="ic ic-green"><svg width="32" height="32" viewBox="0 0 32 32" fill="none" stroke="#479c14" stroke-width="2"><path d="M8 16l8-7 8 7v7H8zM4 27c3-2 5-2 8 0s5 2 8 0 5-2 8 0"/></svg></div>
  <h3>Flood Insurance</h3>
  <p>Provide financial protection against water damage caused by floods, which are often excluded from standard coverage.</p>
</div>
<div class="card" style="left:397px;top:1978px">
  <div class="ic ic-blue"><svg width="32" height="32" viewBox="0 0 32 32" fill="none" stroke="#1d4f9a" stroke-width="2"><circle cx="15" cy="6" r="2"/><path d="M15 9v9h7l3 7M11 15a7 7 0 1 0 9 9"/></svg></div>
  <h3>Disability Insurance</h3>
  <p>Receive income replacement if you're unable to work due to illness or injury, ensuring financial security.</p>
</div>
<div class="card" style="left:607px;top:1978px">
  <div class="ic ic-green"><svg width="32" height="32" viewBox="0 0 32 32"><path d="M16 27S5 20 5 12a5.5 5.5 0 0 1 11-2 5.5 5.5 0 0 1 11 2c0 8-11 15-11 15z" fill="#7cc142"/><path d="M16 12v8M12 16h8" stroke="#fff" stroke-width="2"/></svg></div>
  <h3>Life Insurance</h3>
  <p>Protect your loved ones financially after your passing, covering funeral expenses and ongoing living costs.</p>
</div>
<div class="card" style="left:817px;top:1978px">
  <div class="ic ic-blue"><svg width="32" height="32" viewBox="0 0 32 32"><path d="M16 4l10 4v7c0 7-5 11-10 13C11 26 6 22 6 15V8z" fill="#1d4f9a"/><circle cx="16" cy="15" r="5" fill="#fff"/><path d="M16 12v6M13 15h6" stroke="#1d4f9a" stroke-width="2"/></svg></div>
  <h3>Health Insurance</h3>
  <p>Cover medical expenses, from check-ups to emergencies, ensuring you get the care you need without financial strain.</p>
</div>
<a class="btn btn-green" style="left:539px;top:2248px;width:134px;height:43px">Explore All</a>

<!-- Partners -->
<div class="eyebrow center" style="top:2431px">Our partners</div>
<h2 class="section-title center" style="top:2457px">Trusted Partners for Your Protection</h2>
<div class="partners">
  <span class="partner">VARNIX</span>
  <span class="partner">OSTLE</span>
  <span class="partner">MERIDALE MUTUAL</span>
  <span class="partner">QUILLOR</span>
  <span class="partner">DUNMARROW</span>
  <span class="partner">KGZ</span>
  <span class="partner">PELLWICK</span>
</div>

<!-- Testimonials -->
<div class="eyebrow center" style="top:2664px">Clients testimonials</div>
<h2 class="section-title center" style="top:2689px">Proven Success Stories</h2>

<div class="quote-card" style="left:149px">
  <div class="quote-mark">&#8220;</div>
  <p>It is a long established fact that a reader will be distracted by the readable content of a page when looking at its layout. The point of using Lorem Ipsum is that it has a more-or-less normal distribution of letters, as opposed to using 'Content here, content here'.</p>
  <div class="avatar" role="img" aria-label="Client portrait"></div>
  <h4>Dorian Halvers</h4>
  <div class="stars">
    <svg width="16" height="16" viewBox="0 0 24 24"><path d="M12 2l3 7h7l-5.5 4.5 2 7.5L12 17l-6.5 4 2-7.5L2 9h7z" fill="var(--star)"/></svg>
    <svg width="16" height="16" viewBox="0 0 24 24"><path d="M12 2l3 7h7l-5.5 4.5 2 7.5L12 17l-6.5 4 2-7.5L2 9h7z" fill="var(--star)"/></svg>
    <svg width="16" height="16" viewBox="0 0 24 24"><path d="M12 2l3 7h7l-5.5 4.5 2 7.5L12 17l-6.5 4 2-7.5L2 9h7z" fill="var(--star)"/></svg>
    <svg width="16" height="16" viewBox="0 0 24 24"><path d="M12 2l3 7h7l-5.5 4.5 2 7.5L12 17l-6.5 4 2-7.5L2 9h7z" fill="var(--star)"/></svg>
    <svg width="16" height="16" viewBox="0 0 24 24"><path d="M12 2l3 7h7l-5.5 4.5 2 7.5L12 17l-6.5 4 2-7.5L2 9h7z" fill="var(--star)"/></svg>
  </div>
</div>
<div class="quote-card" style="left:619px">
  <div class="quote-mark">&#8220;</div>
  <p>It is a long established fact that a reader will be distracted by the readable content of a page when looking at its layout. The point of using Lorem Ipsum is that it has a more-or-less normal distribution of letters, as opposed to using 'Content here, content here'.</p>
  <div class="avatar" role="img" aria-label="Client portrait"></div>
  <h4>Milo Trenhart</h4>
  <div class="stars">
    <svg width="16" height="16" viewBox="0 0 24 24"><path d="M12 2l3 7h7l-5.5 4.5 2 7.5L12 17l-6.5 4 2-7.5L2 9h7z" fill="var(--star)"/></svg>
    <svg width="16" height="16" viewBox="0 0 24 24"><path d="M12 2l3 7h7l-5.5 4.5 2 7.5L12 17l-6.5 4 2-7.5L2 9h7z" fill="var(--star)"/></svg>
    <svg width="16" height="16" viewBox="0 0 24 24"><path d="M12 2l3 7h7l-5.5 4.5 2 7.5L12 17l-6.5 4 2-7.5L2 9h7z" fill="var(--star)"/></svg>
    <svg width="16" height="16" viewBox="0 0 24 24"><path d="M12 2l3 7h7l-5.5 4.5 2 7.5L12 17l-6.5 4 2-7.5L2 9h7z" fill="var(--star)"/></svg>
    <svg width="16" height="16" viewBox="0 0 24 24"><path d="M12 2l3 7h7l-5.5 4.5 2 7.5L12 17l-6.5 4 2-7.5L2 9h7z" fill="var(--star)"/></svg>
  </div>
</div>
<div class="arrow" style="left:132px;top:2891px;background:#fff;box-shadow:0 2px 8px rgba(0,0,0,.1)"><svg width="14" height="14" viewBox="0 0 14 14" fill="none" stroke="#7cc142" stroke-width="2"><path d="M12 7H2M6 3L2 7l4 4"/></svg></div>
<div class="arrow" style="left:1049px;top:2891px;background:var(--green-light)"><svg width="14" height="14" viewBox="0 0 14 14" fill="none" stroke="#fff" stroke-width="2"><path d="M2 7h10M8 3l4 4-4 4"/></svg></div>
<div class="dot" style="left:561px"></div>
<div class="dot" style="left:580px"></div>
<div class="dot" style="left:599px;top:3065px;width:14px;height:14px;background:var(--navy)"></div>
<div class="dot" style="left:624px"></div>
<div class="dot" style="left:643px"></div>

<!-- CTA -->
<section class="abs cta" role="img" aria-label="Photo of a family at home, tinted green"></section>
<h2 class="abs center cta-title">Secure a Future with Customized Quote Today!</h2>
<p class="abs cta-text">Protect what matters most with tailored insurance solutions. Get a personalized quote today and secure peace of mind.</p>
<a class="btn btn-navy" style="left:535px;top:3372px;width:143px;height:45px">Get a Quote</a>

<!-- Footer background -->
<footer class="abs footer"></footer>

<!-- Contact form -->
<div class="abs contact-card"></div>
<div class="eyebrow center" style="top:3640px">Contact us</div>
<h2 class="section-title center" style="top:3665px">Get in Touch with Us</h2>
<div class="rule" style="left:569px;top:3712px"></div>
<div class="field" style="left:263px;top:3760px;width:320px">Your First Name <b>*</b></div>
<div class="field" style="left:632px;top:3760px;width:320px">Your Last Name <b>*</b></div>
<div class="field" style="left:263px;top:3830px;width:320px">&nbsp;Enter Your Email Adress <b>*</b></div>
<div class="field" style="left:632px;top:3830px;width:320px">Your Phone Number <b>*</b></div>
<div class="field" style="left:263px;top:3900px;width:689px;height:78px">Your Message</div>
<a class="btn btn-green" style="left:533px;top:4020px;width:147px;height:43px">Submit Now</a>

<!-- Footer content -->
<div class="abs foot-brand"><div class="sq"></div><span>BRELLOW COVER</span></div>
<p class="abs foot-text">Brellow Cover Insurance, we're dedicated to providing you with reliable, comprehensive insurance solutions tailored to your needs.</p>
<div class="social" style="left:931px"></div>
<div class="social g" style="left:980px"></div>
<div class="social" style="left:1028px"></div>
<div class="abs foot-rule"></div>
<div class="abs center" style="top:4316px;color:#fff;font-size:16px;font-weight:600">Contact Information</div>

<div class="info-col" style="left:136px">
  <svg width="22" height="22" viewBox="0 0 24 24"><path d="M6 3l4 4-2 3c1 3 3 5 6 6l3-2 4 4-3 3C10 21 3 14 3 6z" fill="#7cc142"/></svg>
  <h5>Call Us</h5><p>(555)-014-2290</p>
</div>
<div class="abs vdiv" style="left:406px"></div>
<div class="info-col" style="left:442px">
  <svg width="22" height="22" viewBox="0 0 24 24" fill="none" stroke="#7cc142" stroke-width="2"><path d="M12 21s-6-6-6-11a6 6 0 0 1 12 0c0 5-6 11-6 11z"/><circle cx="12" cy="10" r="2"/></svg>
  <h5>Find Us</h5><p>48 Harwick Lane, Suite 210,<br>Bellmore Falls</p>
</div>
<div class="abs vdiv" style="left:780px"></div>
<div class="info-col" style="left:774px">
  <svg width="22" height="22" viewBox="0 0 24 24"><rect x="2" y="5" width="20" height="14" rx="1" fill="#7cc142"/><path d="M2 6l10 7 10-7" stroke="#0b2a80" stroke-width="1.5" fill="none"/></svg>
  <h5>Email Address</h5><p>hello@brellowcover.com</p>
</div>

<div class="abs copyright" style="left:149px">Copyright &copy; 2025 Brellow Cover Insurance - All Rights Reserved.</div>
<div class="abs copyright" style="left:868px">Terms of use &nbsp;&nbsp;&nbsp;&nbsp;&nbsp; Privacy Policy</div>

</body>
</html>
```